TALMORK

The business want a professional looking business card. We have a scetch we will add but want the extra upgrade, and would like more suggestions for variations of our business cards.

```html
<!DOCTYPE html>
<html lang="en">
<head>
<meta charset="utf-8">
<title>TALMORK business card</title>
<link rel="stylesheet" href="https://fonts.googleapis.com/css2?family=Playfair+Display:wght@700&family=Open+Sans:wght@400&display=swap">
<style>
  :root {
    --backdrop: #8e8e8e;
    --card: #1e1e1e;
    --gold: #d6a93a;
    --gold-light: #f0d27a;
    --text-light: #e6e6e6;
    --silver: #bdbdbd;
    --black: #0c0c0c;
  }
  * { margin: 0; padding: 0; box-sizing: border-box; }
  html, body { width: 1200px; height: 1200px; overflow: hidden; background: var(--backdrop); }
  .canvas { position: relative; width: 1200px; height: 1200px; }

  .card {
    position: absolute;
    left: 281px;
    width: 642px;
    height: 366px;
    border-radius: 19px;
    background: var(--card);
    overflow: hidden;
  }
  .card--front { top: 195px; }
  .card--back { top: 639px; }

  .corner-ornament {
    position: absolute; left: 0; top: 0; width: 180px; height: 178px;
    background: radial-gradient(circle at 45% 45%, #3a3a3a 0%, #262626 55%, var(--card) 80%);
  }

  .holder-name {
    position: absolute; left: 45px; top: 176px;
    font-family: "Playfair Display", Georgia, serif; font-weight: 700;
    font-size: 27px; color: var(--gold); letter-spacing: 0.2px;
  }
  .holder-role {
    position: absolute; left: 45px; top: 214px;
    font-family: "Open Sans", Arial, sans-serif; font-size: 16px; color: var(--text-light);
  }
  .divider {
    position: absolute; left: 45px; top: 244px; width: 546px; height: 2px;
    background: linear-gradient(90deg, #b8862a, var(--gold-light), #b8862a);
  }
  .contact-list { position: absolute; left: 45px; top: 261px; list-style: none; }
  .contact-list li {
    display: flex; align-items: center; height: 22.5px;
    font-family: "Open Sans", Arial, sans-serif; font-size: 14.5px; color: var(--text-light);
  }
  .contact-list svg { width: 13px; height: 13px; margin-right: 11px; flex: none; }

  .brand {
    position: absolute; left: 410px; top: 66px; width: 200px; text-align: center;
  }
  .brand-dot {
    display: block; width: 40px; height: 40px; margin: 0 auto 22px;
    border-radius: 50%; background: var(--gold);
  }
  .brand-name {
    font-family: "Playfair Display", Georgia, serif; font-weight: 700;
    font-size: 28px; letter-spacing: 6px; color: var(--gold); line-height: 1;
  }
  .brand-since {
    margin-top: 7px;
    font-family: "Open Sans", Arial, sans-serif; font-size: 9px;
    letter-spacing: 3.5px; color: var(--text-light);
  }

  .pattern-field {
    position: absolute; left: 12px; top: 13px; width: 617px; height: 340px;
    border-radius: 6px;
    background: linear-gradient(90deg, var(--silver) 0%, #6b6b6b 30%, #2e2e2e 55%, var(--black) 100%);
    opacity: 0.55;
  }
</style>
</head>
<body>
<main class="canvas">
  <section class="card card--front">
    <div class="corner-ornament" role="img" aria-label="Large embossed floral ornament in dark tones"></div>

    <div class="brand">
      <span class="brand-dot"></span>
      <div class="brand-name">TALMORK</div>
      <div class="brand-since">SINCE 2026</div>
    </div>

    <h1 class="holder-name">Arvid Solberg Haugland</h1>
    <p class="holder-role">CEO &amp; Founder</p>
    <div class="divider"></div>

    <ul class="contact-list">
      <li>
        <svg viewBox="0 0 24 24" aria-hidden="true"><path fill="#d6a93a" d="M6.6 10.8a15.2 15.2 0 0 0 6.6 6.6l2.2-2.2a1 1 0 0 1 1-.25 11.4 11.4 0 0 0 3.6.57 1 1 0 0 1 1 1V20a1 1 0 0 1-1 1A17 17 0 0 1 3 4a1 1 0 0 1 1-1h3.5a1 1 0 0 1 1 1c0 1.25.2 2.45.57 3.57a1 1 0 0 1-.25 1z"/></svg>
        004791234567
      </li>
      <li>
        <svg viewBox="0 0 24 24" aria-hidden="true"><rect x="2" y="5" width="20" height="14" rx="1.5" fill="#d6a93a"/><path d="M3 6l9 7 9-7" fill="none" stroke="#1e1e1e" stroke-width="1.8"/></svg>
        talmork.llc@mailbox.com
      </li>
      <li>
        <svg viewBox="0 0 24 24" aria-hidden="true"><circle cx="12" cy="12" r="9.5" fill="none" stroke="#d6a93a" stroke-width="2"/><ellipse cx="12" cy="12" rx="4" ry="9.5" fill="none" stroke="#d6a93a" stroke-width="1.6"/><path d="M3 12h18" stroke="#d6a93a" stroke-width="1.6"/></svg>
        www.talmork.llc
      </li>
    </ul>
  </section>

  <section class="card card--back">
    <div class="pattern-field" role="img" aria-label="Repeating grid of embossed floral motifs fading from silver to black, one motif in gold"></div>
  </section>
</main>
</body>
</html>
```